Communication and Marketing agency needs a new presentation card

We are a group of communication and marketing agencies specialized in companies that are in the logistics and industrial sector. The head agency is TELVANO Grupo and the group consists of 4 agencies: TELVANO Media, TELVANO Digital, TELVANO Research and DifundeEnPantalla. We hace 4 offices in Spain (Madrid, Barcelona, Valencia and Murcia). We are looking for a clean and attractive design that transmits our experience, brand presence in the market and knowledge to those who receive the card.It has to maintain the colors of the logo that is attached.
Target Market(s)
logistics and industrial sector
Marketing department
Contact Information for Business Card
Clean and attractive design

```html
<!DOCTYPE html>
<html lang="en">
<head>
<meta charset="utf-8">
<title>TELVANO Digital – Business Card</title>
<link rel="stylesheet" href="https://fonts.googleapis.com/css2?family=Open+Sans:wght@300;400;600;700&display=swap">
<style>
  :root{
    --bg:#24252a;
    --paper:#ffffff;
    --slate:#58585b;
    --slate-line:#4d4d50;
    --brand-red:#be1e34;
    --text-light:#f2f2f2;
    --logo-grey:#4a4a4d;
  }
  *{box-sizing:border-box;margin:0;padding:0}
  html,body{width:1200px;height:960px;overflow:hidden;background:var(--bg);font-family:"Open Sans",Arial,sans-serif}
  .canvas{position:relative;width:1200px;height:960px}
  .card{position:absolute;left:250px;width:700px;height:400px;background:var(--paper);overflow:hidden;box-shadow:0 14px 30px rgba(0,0,0,.45)}
  .card--front{top:60px}
  .card--back{top:500px}

  .wordmark{font-weight:300;color:var(--logo-grey);letter-spacing:2px;white-space:nowrap;display:flex;align-items:center;gap:14px}
  .wordmark__dot{width:14px;height:14px;border-radius:50%;background:var(--brand-red);flex:none}

  .card--front .wordmark{position:absolute;left:0;right:0;top:140px;justify-content:center;font-size:64px}
  .front__url{position:absolute;left:0;right:0;top:268px;text-align:center;font-size:17px;letter-spacing:2px;color:var(--brand-red)}

  .back__art{position:absolute;inset:0}
  .card--back .wordmark{position:absolute;right:42px;top:50px;font-size:40px;letter-spacing:1px;gap:10px}
  .card--back .wordmark__dot{width:10px;height:10px}

  .contact{position:absolute;left:62px;top:214px;color:var(--text-light)}
  .contact__name{font-size:21px;font-weight:700;color:var(--brand-red);letter-spacing:.5px;line-height:1.15}
  .contact__role{font-size:16px;line-height:1.4}
  .contact__list{list-style:none;margin-top:16px}
  .contact__item{display:flex;align-items:center;gap:12px;font-size:16px;line-height:26px}
  .contact__icon{width:14px;height:14px;flex:none;fill:var(--brand-red)}
</style>
</head>
<body>
<main class="canvas">

  <section class="card card--front" aria-label="Card front">
    <div class="wordmark"><span class="wordmark__dot"></span>TELVANO Digital</div>
    <p class="front__url">WWW.TELVANODIGITAL.ES</p>
  </section>

  <section class="card card--back" aria-label="Card back">
    <svg class="back__art" width="700" height="400" viewBox="0 0 700 400" aria-hidden="true">
      <path d="M0,198 C190,140 420,122 505,168 C545,192 565,290 575,400 L0,400 Z" fill="var(--slate)"/>
      <path d="M0,196 C190,138 420,120 505,166 C545,190 565,288 575,400" fill="none" stroke="var(--brand-red)" stroke-width="11"/>
      <path d="M0,182 C170,128 390,98 540,120" fill="none" stroke="var(--slate-line)" stroke-width="6" stroke-linecap="round"/>
    </svg>

    <div class="wordmark"><span class="wordmark__dot"></span>TELVANO Digital</div>

    <div class="contact">
      <p class="contact__name">MARISOL FERRER</p>
      <p class="contact__role">Managing Director</p>
      <ul class="contact__list">
        <li class="contact__item">
          <svg class="contact__icon" viewBox="0 0 16 16"><path d="M3.6 1l2.6 3-1.5 1.8c.9 2 2.5 3.6 4.5 4.5L11 8.8l3 2.6-1.6 3C7 14 2 9 1.6 3.6z"/></svg>
          610.442.3187</li>
        <li class="contact__item">
          <svg class="contact__icon" viewBox="0 0 16 16"><path d="M4 1h8v4H4zM1 6h14v6h-3v3H4v-3H1zm4 4v3h6v-3z"/></svg>
          610.442.3120</li>
        <li class="contact__item">
          <svg class="contact__icon" viewBox="0 0 16 16"><path d="M1 3h14v10H1zm1.5 1.2v.4L8 8.5l5.5-3.9v-.4z"/></svg>
          hola@telvanodigital.es</li>
        <li class="contact__item">
          <svg class="contact__icon" viewBox="0 0 16 16"><path d="M8 1a7 7 0 1 0 0 14A7 7 0 0 0 8 1zm0 1.6c.9 1 1.5 2.6 1.6 4.6H6.4C6.5 5.2 7.1 3.6 8 2.6zM6.4 8.8h3.2c-.1 2-.7 3.6-1.6 4.6-.9-1-1.5-2.6-1.6-4.6z"/></svg>
          www.telvanodigital.es</li>
      </ul>
    </div>
  </section>

</main>
</body>
</html>
```